Financial Advisor Resource Firm needs business card design

Need business card design for company in Omaha NE called Meridale Circle. We provide resources to financial advisors....workshop programs, retirement analysis, and insurance planning. I would like to see designs that use grays, greens, black, and white colors. The final design should communicate 'collaboration' and be simple yet attractive to financial planning clients. I will attached our logo and another picture of a puzzle piece coming together. I would like the incorporate the puzzle picture somehow, maybe on the back somehow, with color or just the gray scale....OR, the picture be the front of the card with 'Meridale' definition on it (see upload) and then company logo, employee name, title, address on the back (see ppt uploaded). The following disclosure needs to be included somewhere- Advisory services offered through Stonebrook Assets, LLC.
Updates

I uploaded a svg and ai file of the logo

Target Market(s)

Financial planning clients and financial advisors....so pretty diverse age range of about 40-70.

Industry/Entity Type

Financial Planning

Contact Information for Business Card

Tobias L. Fenwright, MBA
Founder/President
5287 E. Larkin Road
Suite 230
Omaha, NE 68190
Phone- (402) 555-0147
Cell- (402) 555-0183
Fax- (402) 555-0129
email- tobias@meridaleplan.example
web address- www.meridaleplan.example

Colors
1b1b1b
474747
d3d3d3
ffffff
9bcb3c
abd036

Requirements
Must have
• Must include logo provided, must be 2 sided, and must have disclosure...all of these items listed in project description

```html
<!DOCTYPE html>
<html lang="en">
<head>
<meta charset="utf-8">
<title>Meridale Circle – Business Card</title>
<link rel="stylesheet" href="https://fonts.googleapis.com/css2?family=Poppins:wght@400;600&display=swap">
<style>
  :root {
    --ink: #1b1b1b;
    --charcoal: #2b2b2b;
    --gray: #474747;
    --light-gray: #d3d3d3;
    --paper: #ffffff;
    --green: #9bcb3c;
    --green-alt: #abd036;
    --stage: #e9e9e9;
  }
  * { box-sizing: border-box; margin: 0; padding: 0; }
  html, body { width: 1200px; height: 862px; overflow: hidden; }
  body {
    background: var(--stage);
    font-family: "Poppins", sans-serif;
    display: flex;
    flex-direction: column;
    align-items: center;
    justify-content: center;
    gap: 22px;
  }
  .card {
    width: 700px;
    height: 400px;
    position: relative;
    box-shadow: 0 6px 18px rgba(0,0,0,0.18);
    overflow: hidden;
  }

  /* Back side */
  .card-back { background: var(--charcoal); }
  .card-back .brand {
    position: absolute;
    left: 0; right: 0; top: 150px;
    display: flex; align-items: center; justify-content: center; gap: 14px;
  }
  .brand-dot {
    width: 26px; height: 26px; border-radius: 50%;
    background: var(--green);
    flex: none;
  }
  .brand-name {
    font-weight: 600;
    font-size: 40px;
    letter-spacing: 2px;
    text-transform: uppercase;
    white-space: nowrap;
  }
  .card-back .brand-name { color: var(--paper); }
  .card-back .website {
    position: absolute; left: 0; right: 0; top: 300px;
    text-align: center;
    color: var(--paper);
    font-size: 17px;
    letter-spacing: 0.5px;
  }
  .website .accent { color: var(--green); }

  /* Front side */
  .card-front { background: var(--paper); }
  .card-front .brand {
    position: absolute; left: 36px; top: 182px;
    display: flex; align-items: center; gap: 10px;
  }
  .card-front .brand-dot { width: 18px; height: 18px; }
  .card-front .brand-name { color: var(--ink); font-size: 24px; letter-spacing: 1px; }

  .contact {
    position: absolute; left: 355px; top: 36px;
    border-left: 2px solid var(--green);
    padding-left: 16px;
    height: 220px;
  }
  .contact .name {
    color: var(--green);
    font-weight: 600;
    font-size: 18px;
    text-transform: uppercase;
    letter-spacing: 0.2px;
    white-space: nowrap;
  }
  .contact .title {
    color: var(--gray);
    font-size: 13px;
    margin: 4px 0 14px;
  }
  .contact ul { list-style: none; }
  .contact li {
    display: flex; align-items: center; gap: 10px;
    color: var(--ink);
    font-size: 14px;
    line-height: 25px;
    white-space: nowrap;
  }
  .contact li svg { width: 13px; height: 13px; fill: var(--gray); flex: none; }

  .address-band {
    position: absolute; left: 0; right: 0; top: 300px; height: 72px;
    background: var(--charcoal);
    display: flex; align-items: center; justify-content: center; gap: 10px;
    color: var(--paper);
    font-size: 15px;
  }
  .address-band svg { width: 14px; height: 18px; fill: var(--green); }

  .disclosure {
    position: absolute; left: 0; right: 0; top: 372px; height: 28px;
    display: flex; align-items: center; justify-content: center;
    color: var(--gray);
    font-size: 10px;
    letter-spacing: 0.2px;
  }
</style>
</head>
<body>

<section class="card card-back" aria-label="Card back">
  <div class="brand">
    <span class="brand-dot"></span>
    <span class="brand-name">Meridale Circle</span>
  </div>
  <p class="website">www.<span class="accent">meridaleplan</span>.example</p>
</section>

<section class="card card-front" aria-label="Card front">
  <div class="brand">
    <span class="brand-dot"></span>
    <span class="brand-name">Meridale Circle</span>
  </div>

  <div class="contact">
    <p class="name">Tobias L. Fenwright, MBA</p>
    <p class="title">Founder / President</p>
    <ul>
      <li>
        <svg viewBox="0 0 24 24" aria-hidden="true"><path d="M6.6 10.8a15.1 15.1 0 0 0 6.6 6.6l2.2-2.2a1 1 0 0 1 1-.25 11.4 11.4 0 0 0 3.6.57 1 1 0 0 1 1 1V20a1 1 0 0 1-1 1A17 17 0 0 1 3 4a1 1 0 0 1 1-1h3.5a1 1 0 0 1 1 1c0 1.25.2 2.450.57 3.57a1 1 0 0 1-.25 1z"/></svg>
        (402) 555-0147
      </li>
      <li>
        <svg viewBox="0 0 24 24" aria-hidden="true"><path d="M7 1h10a2 2 0 0 1 2 2v18a2 2 0 0 1-2 2H7a2 2 0 0 1-2-2V3a2 2 0 0 1 2-2zm0 3v14h10V4zm5 15.2a1.2 1.2 0 1 0 0 2.4 1.2 1.2 0 0 0 0-2.4z"/></svg>
        (402) 555-0183
      </li>
      <li>
        <svg viewBox="0 0 24 24" aria-hidden="true"><path d="M7 2h10v5H7zM4 8h16a2 2 0 0 1 2 2v7h-4v5H6v-5H2v-7a2 2 0 0 1 2-2zm4 7v5h8v-5z"/></svg>
        (402) 555-0129
      </li>
      <li>
        <svg viewBox="0 0 24 24" aria-hidden="true"><path d="M2 5h20v14H2zm2 2v.5l8 5 8-5V7zm0 2.8V17h16V9.8l-8 5z"/></svg>
        tobias@meridaleplan.example
      </li>
      <li>
        <svg viewBox="0 0 24 24" aria-hidden="true"><circle cx="12" cy="12" r="9" fill="none" stroke="#474747" stroke-width="2"/><path d="M3 12h18M12 3c3 3 3 15 0 18M12 3c-3 3-3 15 0 18" fill="none" stroke="#474747" stroke-width="1.6"/></svg>
        www.meridaleplan.example
      </li>
    </ul>
  </div>

  <div class="address-band">
    <svg viewBox="0 0 16 22" aria-hidden="true"><path d="M8 0a8 8 0 0 0-8 8c0 6 8 14 8 14s8-8 8-14a8 8 0 0 0-8-8zm0 11a3 3 0 1 1 0-6 3 3 0 0 1 0 6z"/></svg>
    <span>5287 E. Larkin Road Suite 230</span>
  </div>

  <p class="disclosure">Advisory services offered through Stonebrook Assets, LLC.</p>
</section>

</body>
</html>
```